Professional & attention grabbing.

A business card design, front and back. I already have a logo I will attach, but I am open to something new as well.
Things to include:
Name:
Title:
Phone:
Email:
Wanting something that is professional but attention grabbing.
Also we do a lot of work using drones on natural gas pipelines (leading the future)if you want to include any of that. I'm open to ideas.
Target Market(s)
Natural gas transmission industry / greenhouse gas mitigation industry
Industry/Entity Type
Business
Colors
Designer to choose colors to be used in the design.
Look and feel
Each slider illustrates characteristics of the customer's brand and the style your logo design should communicate.

```html
<!DOCTYPE html>
<html lang="en">
<head>
<meta charset="utf-8">
<title>Corvane Inspections – Business Card</title>
<link rel="stylesheet" href="https://fonts.googleapis.com/css2?family=Montserrat:wght@400;500;600;700&display=swap">
<style>
  :root {
    --brand-red: #c0202a;
    --charcoal: #3a3a3c;
    --charcoal-soft: #48484b;
    --paper: #ffffff;
    --backdrop: #c9c9c9;
    --ink: #2e2e30;
  }
  * { margin: 0; padding: 0; box-sizing: border-box; }
  html, body { width: 1200px; height: 1000px; overflow: hidden; }
  body {
    background: var(--backdrop);
    font-family: "Montserrat", sans-serif;
    display: flex;
    align-items: center;
    justify-content: center;
    gap: 60px;
  }
  .card {
    position: relative;
    width: 540px;
    height: 310px;
    box-shadow: 0 4px 14px rgba(0,0,0,0.25);
    overflow: hidden;
  }
  .card--back { background: var(--paper); }
  .card--front {
    background: var(--brand-red);
    display: flex;
    align-items: center;
    justify-content: center;
  }
  .card__band {
    position: absolute;
    top: 0;
    left: 0;
    width: 100%;
    height: 128px;
    background: linear-gradient(180deg, var(--charcoal) 0%, var(--charcoal-soft) 100%);
    border-bottom: 6px solid var(--brand-red);
  }
  .holder {
    position: absolute;
    top: 38px;
    right: 34px;
    text-align: right;
  }
  .holder__name {
    color: var(--paper);
    font-weight: 600;
    font-size: 19px;
    letter-spacing: 1.5px;
  }
  .holder__title {
    color: var(--brand-red);
    font-weight: 600;
    font-size: 12px;
    letter-spacing: 1px;
    margin-top: 5px;
  }
  .brand {
    display: flex;
    align-items: center;
    gap: 10px;
  }
  .brand__square { width: 24px; height: 24px; flex: none; }
  .brand__name {
    font-weight: 700;
    font-size: 22px;
    letter-spacing: 0.3px;
    white-space: nowrap;
  }
  .card--back .brand {
    position: absolute;
    left: 32px;
    top: 178px;
  }
  .card--back .brand__square { background: var(--brand-red); }
  .card--back .brand__name { color: var(--ink); }
  .card--front .brand__square { background: var(--paper); width: 34px; height: 34px; }
  .card--front .brand__name { color: var(--paper); font-size: 32px; }
  .contact {
    position: absolute;
    right: 28px;
    bottom: 26px;
    list-style: none;
  }
  .contact__item {
    display: flex;
    align-items: center;
    justify-content: flex-end;
    gap: 10px;
    color: var(--ink);
    font-size: 14px;
    letter-spacing: 0.6px;
    line-height: 1;
    margin-top: 8px;
  }
  .contact__icon { width: 18px; height: 18px; flex: none; }
</style>
</head>
<body>
  <section class="card card--back" aria-label="Card back">
    <div class="card__band" role="img" aria-label="Charcoal and red wave band across the top of the card"></div>
    <div class="holder">
      <p class="holder__name">DANIEL BROOKE</p>
      <p class="holder__title">FOUNDER</p>
    </div>
    <div class="brand">
      <span class="brand__square"></span>
      <span class="brand__name">Corvane Inspections</span>
    </div>
    <ul class="contact">
      <li class="contact__item">000 000 0000
        <svg class="contact__icon" viewBox="0 0 18 18" aria-hidden="true">
          <rect width="18" height="18" fill="var(--brand-red)"/>
          <path d="M5 4 L7.5 4 L8.3 6.8 L7 7.8 C7.8 9.5 8.8 10.5 10.2 11.2 L11.2 9.9 L14 10.7 L14 13.2 C9 13.6 4.4 9 5 4 Z" fill="#fff"/>
        </svg>
      </li>
      <li class="contact__item">info@yourmail.com
        <svg class="contact__icon" viewBox="0 0 18 18" aria-hidden="true">
          <rect width="18" height="18" fill="var(--brand-red)"/>
          <rect x="3.5" y="5" width="11" height="8" fill="#fff"/>
          <path d="M3.5 5 L9 9.6 L14.5 5" fill="none" stroke="var(--brand-red)" stroke-width="1.1"/>
        </svg>
      </li>
    </ul>
  </section>

  <section class="card card--front" aria-label="Card front">
    <div class="brand">
      <span class="brand__square"></span>
      <span class="brand__name">Corvane Inspections</span>
    </div>
  </section>
</body>
</html>
```